I need a fresh looking, exciting and loaded design for Full service Restaurant

We need a web design for our restaurant, which offers full service Pakistani and Indian food in PA, USA. Design should be elegant, simplified so customers can navigate easily and order food online for catering as well as delivery. We need loads of pictures and room to grow. I already have a web address via vemrilo.com. It should include SSL and e-commerce for ordering food.
Be original and be creative and make it a fun site :)

```html
<!DOCTYPE html>
<html lang="en">
<head>
<meta charset="utf-8">
<title>Masala Haveli – Restaurant</title>
<link href="https://fonts.googleapis.com/css2?family=Lobster&family=Open+Sans:wght@400;600;700&display=swap" rel="stylesheet">
<style>
:root{
  --red:#c8201e;
  --green:#1f7a2c;
  --green-dark:#14501c;
  --ink:#333333;
  --muted:#777777;
  --white:#ffffff;
  --footer:#1e1e1e;
  --hero-a:#2a1a12;
  --hero-b:#5a3220;
}
*{margin:0;padding:0;box-sizing:border-box}
html,body{width:750px;height:1200px;overflow:hidden;background:var(--white)}
body{position:relative;font-family:"Open Sans",Arial,sans-serif;color:var(--ink)}
.script{font-family:"Lobster",Georgia,cursive}

/* hero */
.hero{position:absolute;left:0;top:0;width:750px;height:372px;
  background:radial-gradient(ellipse at 50% 60%,var(--hero-b) 0%,var(--hero-a) 70%,#120a06 100%)}
.logo{position:absolute;top:48px;left:0;width:750px;display:flex;justify-content:center;align-items:center;gap:8px}
.logo-dot{width:14px;height:14px;border-radius:50%;background:var(--red)}
.logo-name{font-family:"Lobster",Georgia,cursive;font-size:26px;color:var(--red)}
.nav{position:absolute;top:150px;left:175px;width:400px;border-top:1px solid rgba(255,255,255,.6);
  display:flex;justify-content:space-between;padding-top:12px}
.nav a{color:var(--white);font-size:9px;font-weight:600;text-decoration:none;letter-spacing:.5px}
.nav a::before{content:"•";margin-right:5px}
.hero-title{position:absolute;top:210px;width:750px;text-align:center;color:var(--white);font-size:42px;font-weight:400}
.hero-sub{position:absolute;top:265px;width:750px;text-align:center;color:var(--white);font-size:12px}
.btn{display:inline-block;background:var(--red);color:var(--white);font-size:9px;font-weight:700;
  padding:7px 14px;letter-spacing:.5px}
.hero .btn{position:absolute;top:296px;left:328px}

/* about */
.about{position:absolute;top:372px;left:0;width:750px;height:290px}
.about-text{position:absolute;left:62px;top:14px;width:385px}
.about h2{color:var(--red);font-size:19px;font-weight:400}
.about h3{color:var(--red);font-size:11px;font-style:italic;font-weight:600;margin:6px 0 12px}
.about p{font-size:7.5px;line-height:1.7;color:var(--muted);margin-bottom:12px}
.about .btn{margin-top:8px}
.steps{position:absolute;left:455px;top:44px;display:flex;flex-direction:column;gap:22px}
.step{width:28px;height:28px;border-radius:50%;background:var(--green);color:var(--white);
  font-size:11px;font-weight:700;display:flex;align-items:center;justify-content:center}
.chef-photo{position:absolute;left:505px;top:0;width:245px;height:290px;
  background:linear-gradient(160deg,#f4f4f4 0%,#e9e2de 60%,#d9cfca 100%)}

/* services */
.services{position:absolute;top:662px;left:0;width:750px;height:222px;
  background:linear-gradient(180deg,#4c7a2a 0%,#2f5a1e 55%,#3d6a26 100%)}
.services h2{position:absolute;top:28px;width:750px;text-align:center;color:var(--white);font-size:18px;font-weight:400}
.services .rule{position:absolute;top:56px;left:355px;width:40px;height:1px;background:rgba(255,255,255,.7)}
.service{position:absolute;top:76px;width:170px;text-align:center;color:var(--white)}
.service .ring{width:64px;height:64px;border-radius:50%;background:var(--white);border:3px solid var(--red);
  margin:0 auto 8px;display:flex;align-items:center;justify-content:center}
.service h4{font-size:9px;font-weight:600}
.service p{font-size:7px;line-height:1.5;margin:3px auto 0;width:150px;opacity:.9}
.scallop{position:absolute;left:0;bottom:-1px;width:750px;height:18px}

/* gallery */
.gallery{position:absolute;top:896px;left:62px;width:330px}
.section-title{color:var(--red);font-size:13px;font-weight:700}
.arrows{position:absolute;top:0;right:0;font-size:10px;color:#999}
.grid{margin-top:16px;display:grid;grid-template-columns:repeat(3,102px);grid-template-rows:repeat(2,78px);gap:10px 12px}
.tile{border-radius:2px}
.t1{background:linear-gradient(135deg,#8a2a1c,#d8a96a)}
.t2{background:linear-gradient(135deg,#3a2a1c,#b86a2c)}
.t3{background:linear-gradient(135deg,#c9b28a,#6a8a3a)}
.t4{background:linear-gradient(135deg,#b8782c,#6a3a1c)}
.t5{background:linear-gradient(135deg,#b02a1c,#e08a3a)}
.t6{background:linear-gradient(135deg,#9a7a4a,#d8c08a)}

/* newsletter */
.newsletter{position:absolute;top:896px;left:500px;width:215px}
.newsletter p{font-size:7.5px;line-height:1.7;color:var(--muted);margin-top:14px}
.field{margin-top:12px;height:22px;border:1px solid #cfcfcf;font-size:7px;color:#999;padding:6px 8px}
.subscribe{margin-top:10px;display:inline-block;background:var(--green-dark);color:var(--white);
  font-size:8px;font-weight:700;padding:7px 14px}

/* footer */
.footer{position:absolute;left:0;top:1138px;width:750px;height:62px;background:var(--footer)}
.footer-links{position:absolute;left:62px;top:18px;font-size:8px;color:#ddd}
.footer-links span{margin:0 4px;color:#888}
.copyright{position:absolute;left:62px;top:36px;font-size:7px;color:#999}
.social{position:absolute;right:62px;top:20px;display:flex;gap:6px}
.social i{width:16px;height:16px;border-radius:50%;background:var(--red);display:block}
</style>
</head>
<body>

<header class="hero" role="img" aria-label="Dark photograph of bowls of colourful spices on a wooden table">
  <div class="logo"><span class="logo-dot"></span><span class="logo-name">Masala Haveli</span></div>
  <nav class="nav">
    <a>HOME</a><a>ABOUT US</a><a>BLOG</a><a>GALLERY</a><a>SERVICES</a><a>CONTACT</a>
  </nav>
  <h1 class="hero-title script">Masala Haveli</h1>
  <p class="hero-sub">At vero eos et accusamus et iusto odio dignissimos ducimus</p>
  <span class="btn">VIEW MORE</span>
</header>

<section class="about">
  <div class="about-text">
    <h2 class="script">On the other hand, we denounce with righteous</h2>
    <h3>At vero eos et accusamus et iusto odio dignissimos ducimus</h3>
    <p>On the other hand, we denounce with righteous indignation and dislike men who are so beguiled and demoralized by the charms of pleasure of the moment, so blinded by desire that they cannot foresee the pain and trouble that are bound to ensue; and equal blame belongs to those who fail in their duty through weakness of will.</p>
    <p>In a free hour, when our power of choice is untrammelled and nothing prevents us from doing what we like best, every pleasure is to be welcomed and every pain avoided. But in certain circumstances it will happen that pleasures must be set aside and annoyances accepted.</p>
    <span class="btn">READ MORE</span>
  </div>
  <div class="steps">
    <span class="step">1</span><span class="step">2</span><span class="step">3</span>
  </div>
  <div class="chef-photo" role="img" aria-label="Photograph of a smiling chef in white uniform and hat holding a ladle"></div>
</section>

<section class="services">
  <h2 class="script">Our Services</h2>
  <span class="rule"></span>

  <div class="service" style="left:65px">
    <div class="ring">
      <svg width="30" height="30" viewBox="0 0 34 34" fill="none" stroke="#444" stroke-width="2">
        <path d="M10 20c-4 0-6-3-6-6s3-6 6-5c1-4 4-5 7-5s6 1 7 5c3-1 6 2 6 5s-2 6-6 6z"/>
        <rect x="10" y="20" width="14" height="8"/>
      </svg>
    </div>
    <h4>Nam libero tempore</h4>
    <p>On the other hand, we denounce with righteous indignation and dislike.</p>
  </div>

  <div class="service" style="left:290px">
    <div class="ring">
      <svg width="30" height="30" viewBox="0 0 34 34" fill="none" stroke="#444" stroke-width="2">
        <path d="M5 12h24c0 7-5 11-12 11S5 19 5 12z"/>
        <line x1="11" y1="21" x2="8" y2="31"/>
        <line x1="23" y1="21" x2="26" y2="31"/>
        <line x1="17" y1="23" x2="17" y2="31"/>
      </svg>
    </div>
    <h4>Nam libero tempore</h4>
    <p>On the other hand, we denounce with righteous indignation and dislike.</p>
  </div>

  <div class="service" style="left:515px">
    <div class="ring">
      <svg width="30" height="30" viewBox="0 0 34 34" fill="none" stroke="#444" stroke-width="2">
        <path d="M11 4v9M8 4v7a3 3 0 0 0 6 0V4M11 14v16"/>
        <path d="M23 4c-3 3-3 10 0 12v14"/>
      </svg>
    </div>
    <h4>Nam libero tempore</h4>
    <p>On the other hand, we denounce with righteous indignation and dislike.</p>
  </div>

  <svg class="scallop" viewBox="0 0 750 20" preserveAspectRatio="none">
    <path fill="#ffffff" d="M0 20 Q15 0 30 20 Q45 0 60 20 Q75 0 90 20 Q105 0 120 20 Q135 0 150 20 Q165 0 180 20 Q195 0 210 20 Q225 0 240 20 Q255 0 270 20 Q285 0 300 20 Q315 0 330 20 Q345 0 360 20 Q375 0 390 20 Q405 0 420 20 Q435 0 450 20 Q465 0 480 20 Q495 0 510 20 Q525 0 540 20 Q555 0 570 20 Q585 0 600 20 Q615 0 630 20 Q645 0 660 20 Q675 0 690 20 Q705 0 720 20 Q735 0 750 20 Z"/>
  </svg>
</section>

<section class="gallery">
  <h2 class="section-title">OUR GALLERY</h2>
  <span class="arrows">‹ ›</span>
  <div class="grid">
    <div class="tile t1" role="img" aria-label="Photo of a plated curry dish"></div>
    <div class="tile t2" role="img" aria-label="Photo of grilled kebabs"></div>
    <div class="tile t3" role="img" aria-label="Photo of a rice and vegetable platter"></div>
    <div class="tile t4" role="img" aria-label="Photo of fried snacks on a plate"></div>
    <div class="tile t5" role="img" aria-label="Photo of tandoori chicken"></div>
    <div class="tile t6" role="img" aria-label="Photo of bread and dips"></div>
  </div>
</section>

<section class="newsletter">
  <h2 class="section-title">NEWSLETTER SIGNUP</h2>
  <p>On the other hand, we denounce with righteous indignation and dislike men who are so beguiled by the charms of pleasure of the moment.</p>
  <div class="field">Email Address</div>
  <span class="subscribe">SUBSCRIBE</span>
</section>

<footer class="footer">
  <div class="footer-links">Home<span>|</span>About Us<span>|</span>Blog<span>|</span>Services<span>|</span>Contact Us</div>
  <div class="copyright">Copyright © 2024 Masala Haveli. All rights reserved.</div>
  <div class="social"><i></i><i></i><i></i></div>
</footer>

</body>
</html>
```